Business Card for Fieldbloom-Eco Friendly Organic Clothing Brand

We are looking for an amazing business card for our eco friendly, organic clothing brand. We are thinking maybe a business card with a peel off sticker on the back, since our hanging clothing tag is a peel off sticker on the back. I will attach our hang tag so we can make sure we stay in line with our design. I've also attached a bag we are doing because I do like the scattered emblem look as well.

```html
<!DOCTYPE html>
<html lang="en">
<head>
<meta charset="utf-8">
<title>Fieldbloom Business Card</title>
<link rel="stylesheet" href="https://fonts.googleapis.com/css2?family=Open+Sans:wght@400;600;700&display=swap">
<style>
  :root {
    --backdrop: #e9e6e1;
    --card-white: #ffffff;
    --ink: #1c1c1a;
    --olive-black: #26271f;
    --slate: #45464a;
    --gold: #e2b21c;
    --gold-deep: #b8860f;
    --gold-light: #f5d76a;
  }
  * { box-sizing: border-box; margin: 0; padding: 0; }
  html, body {
    width: 1200px; height: 900px; overflow: hidden;
    background: var(--backdrop);
    font-family: "Open Sans", Arial, sans-serif;
  }
  .canvas { position: relative; width: 1200px; height: 900px; }

  .card {
    position: absolute;
    width: 640px; height: 366px;
    overflow: hidden;
    box-shadow: 0 8px 22px rgba(0,0,0,0.18);
  }

  /* Back side */
  .card-back { left: 480px; top: 60px; background: var(--olive-black); }
  .back-pattern {
    position: absolute; inset: 0;
    background:
      radial-gradient(circle at 30% 30%, rgba(226,178,28,0.22), transparent 45%),
      radial-gradient(circle at 78% 70%, rgba(226,178,28,0.2), transparent 45%),
      linear-gradient(135deg, #2f302a, #1f201b);
  }
  .back-frame {
    position: absolute; left: 60px; top: 150px; width: 520px; height: 110px;
    border: 3px solid var(--gold);
    display: flex; align-items: center; justify-content: center;
    background: rgba(31,32,27,0.85);
  }
  .back-brand {
    font-weight: 700; font-size: 60px; color: var(--gold); letter-spacing: 1px;
  }

  /* Front side */
  .card-front { left: 80px; top: 480px; background: var(--card-white); }
  .front-shapes { position: absolute; inset: 0; }
  .holder { position: absolute; left: 66px; top: 26px; }
  .holder-name { font-size: 20px; font-weight: 600; color: var(--gold); line-height: 1.15; }
  .holder-role { font-size: 14px; color: var(--ink); }

  .contact { position: absolute; left: 90px; top: 150px; color: var(--ink); font-size: 16px; line-height: 1.3; }
  .contact-address { margin-bottom: 10px; }
  .contact-row { display: flex; align-items: center; gap: 10px; }
  .contact-icon { width: 12px; height: 12px; flex: none; }

  .brand-lockup {
    position: absolute; left: 400px; top: 150px;
    display: flex; flex-direction: column; align-items: flex-start;
  }
  .brand-line { display: flex; align-items: center; gap: 10px; }
  .brand-square { width: 22px; height: 22px; background: var(--gold); }
  .brand-name { font-weight: 700; font-size: 32px; color: var(--olive-black); }
  .brand-url { margin-top: 4px; margin-left: 32px; font-size: 11px; color: var(--slate); }
</style>
</head>
<body>
<main class="canvas">

  <section class="card card-back" aria-label="Card back">
    <div class="back-pattern" role="img" aria-label="Scattered gold words and emblems: Namaste, Peace, Love, live, inspire, Om, peace signs and hearts"></div>
    <div class="back-frame">
      <span class="back-brand">Fieldbloom</span>
    </div>
  </section>

  <section class="card card-front" aria-label="Card front">
    <svg class="front-shapes" width="640" height="366" viewBox="0 0 640 366" aria-hidden="true">
      <polygon points="8,70 40,26 62,26 62,70" fill="var(--gold-deep)"/>
      <polygon points="40,26 62,26 62,40" fill="var(--olive-black)"/>
      <polygon points="0,300 300,300 288,322 0,322" fill="var(--olive-black)"/>
      <polygon points="298,330 640,330 640,366 282,366" fill="var(--slate)"/>
    </svg>

    <div class="holder">
      <p class="holder-name">Daniel Reyes</p>
      <p class="holder-role">Managing Director</p>
    </div>

    <div class="contact">
      <p class="contact-address">12345, Address Goes Here<br>Country Name, 123456.</p>
      <p class="contact-row">
        <svg class="contact-icon" viewBox="0 0 12 12" aria-hidden="true"><path d="M2 1h3l1 3-2 1a7 7 0 0 0 3 3l1-2 3 1v3a1 1 0 0 1-1 1A10 10 0 0 1 1 2a1 1 0 0 1 1-1z" fill="var(--gold)"/></svg>
        044-123 456 789
      </p>
      <p class="contact-row">
        <svg class="contact-icon" viewBox="0 0 12 12" aria-hidden="true"><rect x="0.5" y="2" width="11" height="8" fill="var(--gold)"/><path d="M0.5 2l5.5 4 5.5-4" stroke="#fff" fill="none"/></svg>
        info@webname.com
      </p>
      <p class="contact-row">
        <svg class="contact-icon" viewBox="0 0 12 12" aria-hidden="true"><circle cx="6" cy="6" r="5.5" fill="var(--gold)"/><path d="M0.5 6h11M6 0.5v11" stroke="#fff" stroke-width="0.8"/></svg>
        www.websitename.com
      </p>
    </div>

    <div class="brand-lockup">
      <div class="brand-line">
        <span class="brand-square"></span>
        <span class="brand-name">Fieldbloom</span>
      </div>
      <span class="brand-url">www.fieldbloom.com</span>
    </div>
  </section>

</main>
</body>
</html>
```